Velvet Dice Night Age Verification Landing Page

To create a visually appealing design for the landing page of the adult game "Velvet Dice Night" that confirms the visitor's age.
The design should have a simple and visually appealing look that focuses on two buttons labeled "Yes" and "No". The purpose of the page is to confirm that the visitor is 18 years of age or older before accessing the game's content. Responsive design that works well on desktop and mobile devices. The final output should be delivered in PSD, AI, or Sketch format, along with any necessary images or assets.
I have also attached examples.

```html
<!DOCTYPE html>
<html lang="en">
<head>
<meta charset="UTF-8">
<title>Velvet Dice Night – Age Verification</title>
<link rel="stylesheet" href="https://fonts.googleapis.com/css2?family=Yesteryear&family=Passion+One:wght@400;700&display=swap">
<style>
  :root {
    --bg-light: #d9cdc4;
    --bg-mid: #b79f91;
    --bg-dark: #7c6358;
    --modal: rgba(98, 30, 80, 0.88);
    --frame: #f1e4ec;
    --text: #ffffff;
    --accent: #b8126f;
    --accent-glow: rgba(230, 40, 150, 0.55);
  }
  * { box-sizing: border-box; margin: 0; padding: 0; }
  html, body {
    width: 1200px;
    height: 680px;
    overflow: hidden;
  }
  .page {
    position: relative;
    width: 1200px;
    height: 680px;
    overflow: hidden;
  }
  .backdrop {
    position: absolute;
    inset: 0;
    background:
      radial-gradient(ellipse at 70% 35%, #eee8e3 0%, transparent 45%),
      radial-gradient(ellipse at 40% 75%, #c9a690 0%, transparent 50%),
      linear-gradient(160deg, var(--bg-dark) 0%, var(--bg-mid) 30%, var(--bg-light) 60%, #ece6e1 100%);
  }
  .age-gate {
    position: absolute;
    left: 201px;
    top: 148px;
    width: 798px;
    height: 386px;
    background: var(--modal);
  }
  .age-gate__frame {
    position: absolute;
    left: 13px;
    top: 14px;
    right: 14px;
    bottom: 15px;
    border: 2px solid var(--frame);
    border-radius: 2px;
  }
  .brand {
    position: absolute;
    left: 0;
    right: 0;
    top: 86px;
    text-align: center;
    font-family: "Yesteryear", cursive;
    font-size: 30px;
    line-height: 1;
    color: var(--text);
  }
  .age-gate__question {
    position: absolute;
    left: 0;
    right: 0;
    top: 164px;
    text-align: center;
    font-family: "Yesteryear", cursive;
    font-weight: 400;
    font-size: 31px;
    line-height: 1;
    color: var(--text);
  }
  .age-gate__actions {
    position: absolute;
    left: 304px;
    top: 224px;
    display: flex;
    gap: 14px;
  }
  .btn {
    width: 88px;
    height: 41px;
    border-radius: 21px;
    font-family: "Passion One", sans-serif;
    font-size: 17px;
    letter-spacing: 0.5px;
    color: var(--text);
    display: flex;
    align-items: center;
    justify-content: center;
    text-transform: uppercase;
  }
  .btn--yes {
    background: var(--accent);
    box-shadow: 0 0 8px var(--accent-glow);
  }
  .btn--no {
    border: 2px solid var(--text);
    background: transparent;
  }
  .remember {
    position: absolute;
    left: 306px;
    top: 293px;
    display: flex;
    align-items: center;
    gap: 6px;
    font-family: "Yesteryear", cursive;
    font-size: 22px;
    color: var(--text);
  }
  .remember__radio {
    width: 16px;
    height: 16px;
    border: 1.5px solid var(--text);
    border-radius: 50%;
  }
</style>
</head>
<body>
  <main class="page">
    <div class="backdrop" role="img" aria-label="Soft-focus photo of a couple in a bright hotel bedroom with white sheets"></div>

    <section class="age-gate" aria-labelledby="age-question">
      <div class="age-gate__frame"></div>
      <div class="brand">Velvet Dice Night</div>
      <h1 class="age-gate__question" id="age-question">Are You Over 18 Years Of Age ?</h1>
      <div class="age-gate__actions">
        <span class="btn btn--yes">Yes</span>
        <span class="btn btn--no">No</span>
      </div>
      <div class="remember">
        <span class="remember__radio"></span>
        <span class="remember__label">Remember Me</span>
      </div>
    </section>
  </main>
</body>
</html>
```